Stationery Design Project for Nimbora, Chicago

Nimbora, a street parking application which helps car drivers find a street parking spot by offering an ideal path along which to look for parking. This path is calculated by our algorithm based on data (e.g. historical data, baseball games schedule, etc.). Along this path the driver will find a spot and will also save 70% of the search time. Customer we target is reg. between 21 and 45 yo.

We envision something young, fresh, bright and original. Slightly abstract maybe. It should represent the idea and elements of finding street parking in the city, e.g. car(s), parking spot, people, city, etc. (just ideas!).

Logo is attached.

Requirement:
- Business Cards (2 Sided Full Color CMYK)
- Letterhead (1 Sided Full Color CMYK)
- Envelope (1 Sided Full Color CMYK)
- Sticker (1 Sided Full Color CMYK), round with a 2inch diameter.

Reason: We're starting to get more and more designs and need more time to look into all of them. Very exciting!! Thanks to everybody!

Hi all, we're in the process of selecting our favs. Though choices!!! Really good submissions. Will keep you posted and sorry for the delay.

Target Market(s)

Car drivers and owners between 21 and 45

Industry/Entity Type

Parking

Requirements
Must have
• Sticker should be round and include company URL nimbora.com and the new logo which we will attach soon.
Should not have
• Should not be too serious or boring.

```html
<!DOCTYPE html>
<html lang="en">
<head>
<meta charset="utf-8">
<title>Nimbora Business Card</title>
<link rel="stylesheet" href="https://fonts.googleapis.com/css2?family=PT+Sans:wght@400;700&family=Questrial&display=swap">
<style>
  :root {
    --stage: #b08a2c;
    --card-white: #ffffff;
    --card-grey-light: #d2d2d2;
    --card-grey-dark: #b3b3b3;
    --brand-blue: #1a8fd0;
    --mark-blue: #1f5fc4;
    --ink: #2a2a2a;
    --ink-title: #2d2410;
    --wordmark: #1e1e1e;
  }
  * { margin: 0; padding: 0; box-sizing: border-box; }
  html, body { width: 1200px; height: 686px; overflow: hidden; }
  body {
    background: var(--stage);
    position: relative;
    font-family: "PT Sans", sans-serif;
  }
  .card {
    position: absolute;
    width: 524px;
    height: 299px;
  }
  .card-front { left: 60px; top: 136px; background: var(--card-white); }
  .card-back {
    left: 609px; top: 289px; height: 298px;
    background: radial-gradient(ellipse at 75% 78%, var(--card-grey-light), var(--card-grey-dark) 75%);
  }
  .rule {
    position: absolute;
    top: 127px;
    height: 2px;
    background: var(--brand-blue);
  }
  .rule-left { left: 0; width: 36px; }
  .rule-mid { left: 291px; width: 172px; }
  .rule-right { left: 495px; width: 29px; }
  .brand {
    position: absolute;
    display: flex;
    align-items: center;
  }
  .brand-dot {
    border-radius: 50%;
    background: var(--mark-blue);
    flex: none;
  }
  .brand-name {
    font-family: "PT Sans", sans-serif;
    font-weight: 700;
    color: var(--wordmark);
    line-height: 1;
  }
  .card-front .brand { left: 50px; top: 93px; gap: 10px; }
  .card-front .brand-dot { width: 68px; height: 68px; }
  .card-front .brand-name { font-size: 36px; }
  .card-back .brand { left: 89px; top: 107px; gap: 14px; }
  .card-back .brand-dot { width: 102px; height: 102px; }
  .card-back .brand-name { font-size: 58px; }
  .person {
    position: absolute;
    right: 61px;
    top: 73px;
    text-align: right;
  }
  .person-name {
    color: var(--brand-blue);
    font-weight: 700;
    font-size: 16px;
    line-height: 20px;
  }
  .person-title {
    color: var(--ink-title);
    font-weight: 700;
    font-size: 12.5px;
    line-height: 16px;
  }
  .contact {
    position: absolute;
    right: 62px;
    top: 147px;
    list-style: none;
    text-align: right;
    font-size: 13px;
    color: var(--ink);
  }
  .contact li {
    display: flex;
    justify-content: flex-end;
    align-items: center;
    gap: 5px;
    height: 18px;
  }
  .contact li:first-child { margin-bottom: 3px; }
  .contact svg { width: 12px; height: 12px; fill: var(--brand-blue); flex: none; }
  .address {
    position: absolute;
    right: 56px;
    top: 224px;
    font-size: 13px;
    color: var(--ink);
  }
</style>
</head>
<body>
  <section class="card card-front">
    <div class="rule rule-left"></div>
    <div class="rule rule-mid"></div>
    <div class="rule rule-right"></div>

    <div class="brand">
      <span class="brand-dot"></span>
      <span class="brand-name">Nimbora</span>
    </div>

    <div class="person">
      <p class="person-name">Your Name</p>
      <p class="person-title">Title</p>
    </div>

    <ul class="contact">
      <li>123-456-7890
        <svg viewBox="0 0 24 24" aria-hidden="true"><path d="M6.6 10.8a15 15 0 0 0 6.6 6.6l2.2-2.2c.3-.3.7-.4 1-.2 1.1.4 2.3.6 3.6.6.6 0 1 .4 1 1V20c0 .6-.4 1-1 1A17 17 0 0 1 3 4c0-.6.4-1 1-1h3.5c.6 0 1 .4 1 1 0 1.3.2 2.5.6 3.6.1.3 0 .7-.2 1z"/></svg>
      </li>
      <li>123-456-7890
        <svg viewBox="0 0 24 24" aria-hidden="true"><path d="M6 2h9l3 3v4H6zM3 10h18v8h-3v4H6v-4H3zm5 6v4h8v-4z"/></svg>
      </li>
      <li>name@website.com
        <svg viewBox="0 0 24 24" aria-hidden="true"><path d="M2 5h20v14H2zm2 2v.5l8 5 8-5V7z"/></svg>
      </li>
      <li>www.website.com
        <svg viewBox="0 0 24 24" aria-hidden="true"><path d="M12 2a10 10 0 1 0 0 20 10 10 0 0 0 0-20zm6.9 6h-3a15 15 0 0 0-1.3-3.9A8 8 0 0 1 18.9 8zM12 4c.8 1.1 1.5 2.5 1.9 4h-3.8c.4-1.5 1.1-2.9 1.9-4zM4.3 14a8 8 0 0 1 0-4h3.4a16 16 0 0 0 0 4zm.8 2h3a15 15 0 0 0 1.3 3.9A8 8 0 0 1 5.1 16zm3-8h-3a8 8 0 0 1 4.3-3.9C8.8 5.3 8.4 6.6 8.1 8zM12 20c-.8-1.1-1.5-2.5-1.9-4h3.8c-.4 1.5-1.1 2.9-1.9 4zm2.3-6H9.7a14 14 0 0 1 0-4h4.6a14 14 0 0 1 0 4zm.3 5.9c.6-1.2 1-2.5 1.3-3.9h3a8 8 0 0 1-4.3 3.9zm1.7-5.9a16 16 0 0 0 0-4h3.4a8 8 0 0 1 0 4z"/></svg>
      </li>
    </ul>

    <p class="address">Street name City State, zip code</p>
  </section>

  <section class="card card-back">
    <div class="brand">
      <span class="brand-dot"></span>
      <span class="brand-name">Nimbora</span>
    </div>
  </section>
</body>
</html>
```